Book cover design for a collection of poetry - The Lanternfield

Book cover and back design need to be moody, nostalgic, reflective, ethereal. Melancholy and other worldly. Cover design should not be time specific to a period or place but if applicable should reflect British landscape. Book cover should be in tones of blue and must include the title and author (THE LANTERNFIELD BY CORBIN WHITLACE). We love the idea of rain, and looking out of a window. See attached designs. A world you are observing but not in.

Industry/Entity Type

Book Publisher

Font styles to use
Serif
Script

Colors
3176b5
3377b5
85acd3
eaf1f7
0792cd
33a6d7
86cae7
ecf7fb
86cfc6

Requirements
Must have
• The colour blue in it, must be melancholy and reflective.
Nice to have
• Rain in the cover.
Should not have
• Any bright colours.

```html
<!DOCTYPE html>
<html lang="en">
<head>
<meta charset="utf-8">
<title>The Lanternfield — Cover and Back</title>
<link href="https://fonts.googleapis.com/css2?family=Abril+Fatface&family=Playfair+Display:wght@700;900&family=Arimo:wght@400&display=swap" rel="stylesheet">
<style>
  :root {
    --paper: #ffffff;
    --navy: #02163f;
    --frame: #ffffff;
    --panel-light: #f3f8fa;
    --panel-shade: #c9d6df;
    --blurb: #0aa6e6;
    --title-shadow: #1a2fe0;
    --forest-dark: #0b2a3a;
    --forest-green: #2f7f58;
    --sky-mint: #a6ecdf;
    --rain-blue: #2f63c8;
    --rain-pale: #8fb3e8;
  }
  * { margin: 0; padding: 0; box-sizing: border-box; }
  html, body { width: 1200px; height: 820px; overflow: hidden; background: var(--paper); }
  .spread { position: relative; width: 1200px; height: 820px; background: var(--paper); }

  /* Front cover */
  .front-cover {
    position: absolute; left: 0; top: 0; width: 586px; height: 820px;
    overflow: hidden; border: 1px solid #1b2333;
  }
  .front-cover__scene {
    position: absolute; inset: 0;
    background:
      radial-gradient(ellipse 120px 120px at 20px 40px, rgba(230,255,250,0.9), rgba(166,236,223,0) 100%),
      linear-gradient(90deg, rgba(166,236,223,0.75) 0%, rgba(80,150,130,0.4) 14%, rgba(11,42,58,0) 28%),
      radial-gradient(ellipse 260px 300px at 300px 280px, rgba(47,127,88,0.85), rgba(20,60,50,0) 100%),
      linear-gradient(90deg, rgba(11,42,58,0) 60%, rgba(8,20,50,0.9) 80%, rgba(20,40,90,0.6) 100%),
      linear-gradient(180deg, var(--forest-dark) 0%, #15453a 45%, #2c5e7e 62%, var(--rain-blue) 78%, #3b6fd0 90%, var(--rain-pale) 100%);
  }
  .front-cover__title {
    position: absolute; left: 0; right: 0; top: 142px;
    text-align: center; color: var(--paper);
    font-family: "Abril Fatface", "Playfair Display", serif;
    text-shadow: -3px 2px 0 var(--title-shadow);
  }
  .front-cover__title-small { display: block; font-size: 92px; line-height: 96px; }
  .front-cover__title-large { display: block; font-size: 60px; line-height: 80px; margin-top: 20px; letter-spacing: 0.5px; }
  .front-cover__band {
    position: absolute; left: 0; width: 586px; top: 655px; height: 63px;
    border-top: 2px solid var(--paper); border-bottom: 2px solid var(--paper);
    display: flex; align-items: center; justify-content: center;
  }
  .front-cover__author {
    font-family: "Playfair Display", serif; font-weight: 900;
    font-size: 28px; letter-spacing: 1.5px; color: var(--paper);
    transform: scaleX(0.88);
  }

  /* Back cover */
  .back-cover {
    position: absolute; left: 615px; top: 0; width: 585px; height: 820px;
    background: var(--navy);
  }
  .back-cover__frame {
    position: absolute; left: 40px; top: 54px; width: 505px; height: 711px;
    border: 3px solid var(--frame);
  }
  .back-cover__panel {
    position: absolute; left: 0; right: 0; top: 130px; height: 432px;
    background: linear-gradient(180deg, var(--panel-shade) 0%, var(--panel-light) 14%, var(--panel-light) 86%, var(--panel-shade) 100%);
    border-radius: 60px 60px 60px 60px / 30px 30px 30px 30px;
  }
  .back-cover__ornament {
    position: absolute; left: 140px; width: 220px;
    background: linear-gradient(180deg, rgba(240,246,250,0.95), rgba(130,150,185,0.6));
    border-radius: 40px;
  }
  .back-cover__ornament--top { top: 8px; height: 172px; }
  .back-cover__ornament--bottom { top: 508px; height: 188px; transform: scaleY(-1); }
  .back-cover__blurb {
    position: absolute; left: 40px; right: 0; top: 268px;
    text-align: center; color: var(--blurb);
    font-family: "Arimo", Arial, sans-serif; font-size: 11.5px;
    line-height: 16.7px; letter-spacing: 1.6px;
  }
  .back-cover__blurb p + p { margin-top: 16.7px; }
  .back-cover__blurb span { display: block; white-space: nowrap; }
</style>
</head>
<body>
<div class="spread">
  <section class="front-cover">
    <div class="front-cover__scene" role="img" aria-label="Painted forest path in the rain, tall blue trees and soft green foliage with rain-speckled ground"></div>
    <h1 class="front-cover__title">
      <span class="front-cover__title-small">THE</span>
      <span class="front-cover__title-large">LANTERNFIELD</span>
    </h1>
    <div class="front-cover__band">
      <p class="front-cover__author">CORBIN WHITLACE</p>
    </div>
  </section>

  <section class="back-cover">
    <div class="back-cover__frame">
      <div class="back-cover__panel" role="img" aria-label="Pale scalloped filigree panel"></div>
      <div class="back-cover__ornament back-cover__ornament--top" role="img" aria-label="Ornamental scrollwork crest"></div>
      <div class="back-cover__ornament back-cover__ornament--bottom" role="img" aria-label="Ornamental scrollwork crest"></div>
    </div>
    <div class="back-cover__blurb">
      <p><span>THE LANTERNFIELD IS A COLLECTION OF POETRY.</span></p>
      <p>
        <span>TOLD IN TWO PARTS WE FIRST MEET CHARLES –</span>
        <span>AGED, CRIPPLED AND LEFT ALONE IN HIS</span>
        <span>INHERITED MARSH HOUSE - REFLECTING ON HIS</span>
        <span>LIFE AND HIS MARRIAGE TO BEAUTIFUL ALICE</span>
        <span>WHO WE MEET IN PART TWO. ALICE IS SUICIDAL,</span>
        <span>MANICALLY DEPRESSED AND STRUGGLING WITH</span>
        <span>LIFE AS A WIFE AND MOTHER. SHE MEETS,</span>
        <span>HARBORS AND FALLS IN LOVE WITH A SOLDIER</span>
        <span>DURING WWII AND HER WORLD IS CHANGED</span>
        <span>FOREVER.</span>
      </p>
      <p>
        <span>MOVING THROUGH THE 20TH CENTURY, THIS LIFE</span>
        <span>AND THE NEXT, THE LANTERNFIELD INTERWEAVES</span>
        <span>GRIEF, LOSS, THE AFTER-LIFE, MENTAL ILLNESS,</span>
        <span>AND ULTIMATELY THE TRUE NATURE OF LOVE.</span>
      </p>
    </div>
  </section>
</div>
</body>
</html>
```